Website mockup using figma or other design software for Plumbing Company

We are looking for a talented UI/UX designer to create a high-converting, modern, and professional website design for a local plumbing company. The goal is to move away from the "dated" look of traditional trades and provide a seamless, trustworthy experience for homeowners and commercial clients.
The Challenge
Create a Homepage and a Service Page design that balances professional expertise with an urgent "call-to-action" (CTA) focus. We need a design that looks great on desktop but is built with a mobile-first mindset, as most customers find plumbers via their phones during emergencies.
This company will focus more on B2B, and corporate contracts, but should still be friendly to the public.
Here are some examples of what we are looking for
https://velotrin-works.com/construction/plumbing-construction/
https://velotrin-works.com/
The company is called "KT Plumbing."
Please see the logo below.

```html
<!DOCTYPE html>
<html lang="en">
<head>
<meta charset="utf-8">
<title>Velotrin Works – MEP Services</title>
<link href="https://fonts.googleapis.com/css2?family=Roboto:wght@400;500;700;900&family=Arimo:wght@400;700&display=swap" rel="stylesheet">
<style>
:root{
  --blue:#0a6bbd;
  --blue-bright:#1479cc;
  --navy:#0d1e33;
  --navy-deep:#0a1729;
  --ink:#111;
  --text:#2a2a2a;
  --muted:#666;
  --white:#fff;
  --line:#d9d9d9;
}
*{margin:0;padding:0;box-sizing:border-box}
html,body{width:1200px;height:3727px;overflow:hidden}
body{position:relative;background:var(--white);font-family:"Arimo",Arial,sans-serif;color:var(--text)}
.abs{position:absolute}
h1,h2,h3,.head{font-family:"Roboto",Arial,sans-serif}

/* top bar */
.topbar{left:0;top:0;width:1200px;height:48px;background:var(--blue);color:var(--white);font:700 13px "Roboto",sans-serif}
.topbar .soc{top:13px;width:20px;height:20px;border:2px solid var(--white);border-radius:50%}
.topbar .info{top:16px;display:flex;align-items:center;gap:10px}

/* nav */
.brand{display:flex;align-items:center;gap:12px;font:900 38px "Roboto",sans-serif;color:var(--blue);letter-spacing:1px}
.brand .mark{width:46px;height:46px;background:var(--blue)}
.nav a{position:absolute;top:82px;font:500 14px "Roboto",sans-serif;color:var(--ink);text-decoration:none;letter-spacing:.3px}
.nav a.active{color:var(--blue)}
.btn{display:flex;align-items:center;justify-content:center;font:700 14px "Roboto",sans-serif;color:var(--white);background:var(--blue);transform:skewX(-18deg);text-decoration:none}
.btn span{transform:skewX(18deg)}

/* hero */
.hero-photo{left:0;top:132px;width:700px;height:603px;background:linear-gradient(135deg,#8e8f8f,#c9c6c1 45%,#6f6c68)}
.hero-dark{left:0;top:132px;width:1200px;height:603px}
.hero h1{left:677px;top:232px;width:420px;font-size:48px;line-height:56px;font-weight:700;color:var(--white);letter-spacing:.5px}
.hero p{left:677px;top:466px;width:400px;font-size:15px;line-height:24px;color:var(--white)}

/* section titles */
.sec-title{width:1200px;left:0;text-align:center;font:500 34px "Roboto",sans-serif;color:var(--ink)}
.sec-title b{color:var(--blue);font-weight:500}
.underline{width:56px;height:3px;background:var(--navy)}

/* services */
.svc-intro{left:0;width:1200px;top:898px;text-align:center;font-size:15px;line-height:25px;color:var(--ink)}
.card{top:984px;height:403px}
.card .panel{position:absolute;inset:0;background:var(--white);transform:skewX(-10deg);box-shadow:0 8px 22px rgba(0,0,0,.16);border-left:3px solid var(--navy)}
.card .pic{position:absolute;top:18px;height:185px;transform:skewX(-10deg)}
.card h3{position:absolute;top:226px;left:0;width:100%;text-align:center;font-size:19px;line-height:26px;font-weight:700;color:var(--ink);letter-spacing:.3px}
.card p{position:absolute;top:284px;left:0;width:100%;text-align:center;font-size:15px;line-height:26px;color:var(--ink)}
.card .more{position:absolute;top:342px;left:0;width:100%;text-align:center;font-size:17px;color:var(--ink);text-decoration:underline}
.card .more.hi{color:var(--blue)}

/* about */
.about{left:0;top:1491px;width:1200px;height:598px;background:linear-gradient(90deg,#0b63b0,#1275c6 55%,#1a7bcc)}
.about-pic{left:108px;top:1611px;width:484px;height:358px;clip-path:polygon(93px 0,100% 0,407px 100%,0 100%);background:linear-gradient(135deg,#e9e9e9,#5b7fb8 45%,#2d4f8a)}
.about h2{left:644px;top:1606px;font-size:33px;font-weight:700;color:var(--white)}
.about .bar{left:644px;top:1655px;width:50px;height:3px;background:var(--white)}
.about p{left:644px;width:450px;font-size:15px;line-height:25px;color:var(--white)}
.btn-white{background:var(--white);color:var(--ink)}

/* why */
.why-intro{left:140px;width:920px;top:2232px;text-align:center;font-size:17px;line-height:27px;color:var(--ink)}
.feat{font:700 20px "Roboto",sans-serif;color:var(--ink);line-height:26px}
.feat.l{text-align:right}
.ico{width:70px;height:70px;border-radius:50%;background:var(--navy);border:4px solid var(--white);box-shadow:0 0 0 2px var(--navy);display:flex;align-items:center;justify-content:center}

/* request */
.req-bg{left:0;top:2776px;width:1200px;height:572px;background:linear-gradient(90deg,#2a3a4f 0,#0f2238 50%,#0a1729 100%)}
.req-photo{left:0;top:2750px;width:560px;height:598px;background:linear-gradient(110deg,#b98b6d,#8a7a70 35%,#bfc3c6 60%,rgba(16,34,56,0) 100%)}
.req h2{left:547px;top:2840px;font:500 28px "Roboto",sans-serif;color:var(--white)}
.req .bar{left:547px;top:2890px;width:52px;height:3px;background:var(--white)}
.field{height:41px;background:var(--white);font-size:13px;color:#444;padding:14px 12px 0}
.field.sel::after{content:"";position:absolute;right:14px;top:18px;border:5px solid transparent;border-top-color:#333}

/* footer */
.foot-title{font:500 15px "Roboto",sans-serif;color:var(--ink)}
.foot-link{font-size:13px;color:#555}
.vline{width:2px;background:var(--line)}
.vline::before{content:"";position:absolute;left:-1px;top:0;width:4px;height:44px;background:var(--blue)}
.fsoc{width:30px;height:30px;border:1px solid #bbb;border-radius:50%}
.contact-row{display:flex;align-items:flex-start;gap:12px;font-size:14px;line-height:24px;color:#444}
</style>
</head>
<body>

<!-- top bar -->
<div class="abs topbar">
  <div class="abs soc" style="left:126px"></div>
  <div class="abs soc" style="left:172px"></div>
  <div class="abs soc" style="left:222px"></div>
  <div class="abs soc" style="left:278px"></div>
  <div class="abs soc" style="left:328px"></div>
  <div class="abs info" style="left:522px">
    <svg width="20" height="14" viewBox="0 0 20 14"><rect x="1" y="1" width="18" height="12" fill="none" stroke="#fff" stroke-width="2"/><path d="M1 1l9 7 9-7" fill="none" stroke="#fff" stroke-width="2"/></svg>
    EMAIL: info@velotrinworks.com
  </div>
  <div class="abs info" style="left:825px">
    <svg width="16" height="16" viewBox="0 0 24 24"><path fill="#fff" d="M6.6 10.8a15 15 0 006.6 6.6l2.2-2.2c.3-.3.7-.4 1-.2 1.1.4 2.3.6 3.6.6.6 0 1 .4 1 1V20c0 .6-.4 1-1 1A17 17 0 013 4c0-.6.4-1 1-1h3.5c.6 0 1 .4 1 1 0 1.3.2 2.5.6 3.6.1.3 0 .7-.2 1z"/></svg>
    GENERAL INQUIRIES: 916-555-0142
  </div>
</div>

<!-- nav -->
<div class="abs brand" style="left:101px;top:68px"><span class="mark"></span>VELOTRIN</div>
<nav class="nav">
  <a class="active" style="left:527px">HOME</a>
  <a style="left:597px">ABOUT</a>
  <a style="left:673px">SERVICES</a>
  <a style="left:773px">BLOG</a>
  <a style="left:840px">PROJECTS</a>
</nav>
<a class="abs btn" style="left:945px;top:69px;width:148px;height:42px"><span>CONTACT US</span></a>

<!-- hero -->
<section class="hero">
  <div class="abs hero-photo" role="img" aria-label="Plumber in safety glasses working on a wall-mounted pipe valve in a tiled washroom"></div>
  <svg class="abs hero-dark" width="1200" height="603" viewBox="0 0 1200 603">
    <polygon points="669,0 1200,0 1200,603 562,603" fill="#0a1a2e"/>
    <polygon points="658,0 672,0 565,603 551,603" fill="#0a6bbd"/>
    <polygon points="760,112 1180,112 1030,495 640,495" fill="#132840" opacity=".55"/>
  </svg>
  <h1 class="abs">PROVIDING MEP EXPERTISE FROM CONCEPT TO MAINTENANCE</h1>
  <p class="abs">Velotrin Works is leading the evolution of construction. Each day we wake up and show up with a charge to fulfill our mission.</p>
  <a class="abs btn" style="left:683px;top:560px;width:148px;height:40px"><span>CONTACT US</span></a>
</section>

<!-- services -->
<h2 class="abs sec-title" style="top:824px">OUR <b>SERVICES</b></h2>
<div class="abs underline" style="left:572px;top:873px"></div>
<p class="abs svc-intro">VW Service offers a single point of contact for reliable service, maintenance, installations, and repairs across multiple trades.<br>Our customer-focused certified technicians provide our clients with solutions to all their mechanical/HVAC, electrical,</p>

<div class="abs card" style="left:90px;width:380px">
  <div class="panel"></div>
  <div class="pic" role="img" aria-label="Hands tightening a leaking metal pipe fitting" style="left:58px;width:292px;background:linear-gradient(135deg,#3e5567,#a7b3bd 50%,#2f3d48)"></div>
  <h3>PIPE INSTALLATION &amp;<br>REPLACEMENT</h3>
  <p>From preventative maintenance to<br>24/7 emergency service VW Service</p>
  <div class="more">Read More ➜</div>
</div>
<div class="abs card" style="left:440px;width:340px">
  <div class="panel"></div>
  <div class="pic" role="img" aria-label="Technician in hard hat and safety vest inspecting copper pipes" style="left:40px;width:286px;background:linear-gradient(135deg,#8a6a4a,#c9b28a 45%,#9aa36a)"></div>
  <h3>LEAK DETECTION &amp;<br>REPAIR</h3>
  <p>From preventative maintenance to<br>24/7 emergency service VW Service</p>
  <div class="more hi">Read More ➜</div>
</div>
<div class="abs card" style="left:780px;width:340px">
  <div class="panel"></div>
  <div class="pic" role="img" aria-label="Workers in orange gear clearing a street drain with a hose" style="left:38px;width:286px;background:linear-gradient(135deg,#2b3138,#d06a26 45%,#3a4148)"></div>
  <h3>DRAIN CLEANING &amp;<br>BLOCK REMOVAL</h3>
  <p>From preventative maintenance to<br>24/7 emergency service VW Service</p>
  <div class="more">Read More ➜</div>
</div>

<!-- about -->
<section>
  <div class="abs about"></div>
  <div class="abs about-pic" role="img" aria-label="Plumber in a blue cap fixing pipes beneath a sink"></div>
  <h2 class="abs about" style="left:644px;top:1606px;width:auto;height:auto;background:none;font-size:33px;font-weight:700;color:#fff">ABOUT US</h2>
  <div class="abs" style="left:644px;top:1655px;width:50px;height:3px;background:#fff"></div>
  <p class="abs" style="left:644px;top:1690px;width:450px;font-size:15px;line-height:25px;color:#fff">Velotrin Works is leading the evolution of construction. Each day we wake up and show up with a charge to fulfill our mission.</p>
  <p class="abs" style="left:644px;top:1752px;width:450px;font-size:15px;line-height:25px;color:#fff">Velotrin Works takes a big-picture approach to the construction process by self-performing electrical, HVAC, plumbing, process piping, underground utilities, prefabrication, and MEP design. Instead of multiple consultants and countless subcontractors, our customers work with just one company to eliminate profit layers, scope gaps, and complexity of schedules.</p>
  <a class="abs btn btn-white" style="left:650px;top:1925px;width:150px;height:40px"><span>READ MORE</span></a>
</section>

<!-- why choose us -->
<h2 class="abs sec-title" style="top:2168px">WHY <b>CHOOSE US</b></h2>
<div class="abs underline" style="left:576px;top:2217px"></div>
<p class="abs why-intro">Velotrin Works takes a big-picture approach to the construction process by self-performing electrical, HVAC, plumbing, process piping, underground utilities, prefabrication, and MEP design.</p>

<svg class="abs" style="left:0;top:2300px" width="1200" height="380" viewBox="0 0 1200 380">
  <polygon points="499,23 796,23 627,358 330,358" fill="#0a6bbd"/>
</svg>

<div class="abs feat l" style="left:107px;top:2370px;width:300px">Water Heater (Geyser)<br>Installation &amp; Repair</div>
<div class="abs ico" style="left:417px;top:2368px"><svg width="30" height="30" viewBox="0 0 24 24"><path fill="#fff" d="M13 2L4 14h7l-1 8 9-12h-7z"/></svg></div>
<div class="abs feat l" style="left:59px;top:2466px;width:300px">Drain Cleaning &amp; Block<br>Removal</div>
<div class="abs ico" style="left:369px;top:2462px"><svg width="28" height="28" viewBox="0 0 24 24" fill="none" stroke="#fff" stroke-width="2"><rect x="4" y="4" width="16" height="16" rx="2"/><path d="M8 12h8"/></svg></div>
<div class="abs feat l" style="left:2px;top:2560px;width:300px">Leak Detection &amp;<br>Repair</div>
<div class="abs ico" style="left:312px;top:2556px"><svg width="28" height="28" viewBox="0 0 24 24"><circle cx="12" cy="8" r="4" fill="#fff"/><path d="M4 21c0-4 4-7 8-7s8 3 8 7z" fill="#fff"/></svg></div>

<div class="abs ico" style="left:732px;top:2368px"><svg width="28" height="28" viewBox="0 0 24 24" fill="#fff"><rect x="5" y="10" width="14" height="10" rx="1"/><rect x="10" y="4" width="4" height="6"/></svg></div>
<div class="abs feat" style="left:814px;top:2374px">Bathroom &amp; Kitchen<br>Fitting Installation</div>
<div class="abs ico" style="left:679px;top:2462px"><svg width="28" height="28" viewBox="0 0 24 24"><path fill="#fff" d="M14.7 6.3a4 4 0 015 5l-8.5 8.5-3-3 8.5-8.5zM4 17l3 3-3 1z"/></svg></div>
<div class="abs feat" style="left:760px;top:2484px">Plumbing</div>
<div class="abs ico" style="left:632px;top:2556px"><svg width="28" height="28" viewBox="0 0 24 24" fill="none" stroke="#fff" stroke-width="2.4"><path d="M6 20V10h12v10M12 10V4"/></svg></div>
<div class="abs feat" style="left:713px;top:2578px">Pipe Installation</div>

<!-- request service -->
<section class="req">
  <div class="abs req-bg"></div>
  <div class="abs req-photo" role="img" aria-label="Bearded plumber in a cap servicing a water heater tank"></div>
  <h2 class="abs">REQUEST SERVICE OR ESTIMATE</h2>
  <div class="abs bar"></div>
  <div class="abs field" style="left:547px;top:2921px;width:267px">Name</div>
  <div class="abs field" style="left:832px;top:2921px;width:267px">Email</div>
  <div class="abs field" style="left:547px;top:2983px;width:267px">Phone</div>
  <div class="abs field" style="left:832px;top:2983px;width:267px">Address</div>
  <div class="abs field" style="left:547px;top:3046px;width:267px">City/Town</div>
  <div class="abs field sel" style="left:832px;top:3046px;width:267px">Service Needed</div>
  <div class="abs field" style="left:547px;top:3109px;width:552px;height:87px">Comment</div>
  <a class="abs btn" style="left:550px;top:3219px;width:142px;height:40px"><span>SUBMIT</span></a>
</section>

<!-- footer -->
<footer>
  <div class="abs brand" style="left:98px;top:3467px;font-size:34px"><span class="mark" style="width:42px;height:42px"></span>VELOTRIN</div>
  <div class="abs fsoc" style="left:210px;top:3533px"></div>
  <div class="abs fsoc" style="left:250px;top:3533px"></div>
  <div class="abs fsoc" style="left:290px;top:3533px"></div>

  <div class="abs vline" style="left:428px;top:3442px;height:194px"></div>
  <div class="abs foot-title" style="left:482px;top:3441px">QUICK LINKS</div>
  <div class="abs foot-link" style="left:482px;top:3484px">Home</div>
  <div class="abs foot-link" style="left:482px;top:3509px">About</div>
  <div class="abs foot-link" style="left:482px;top:3534px">Services</div>
  <div class="abs foot-link" style="left:482px;top:3559px">Blog</div>
  <div class="abs foot-link" style="left:482px;top:3584px">Contact</div>
  <div class="abs foot-link" style="left:585px;top:3484px">Our People</div>
  <div class="abs foot-link" style="left:585px;top:3509px">Case Studies</div>
  <div class="abs foot-link" style="left:585px;top:3534px">Careers</div>
  <div class="abs foot-link" style="left:585px;top:3559px">Terms &amp; Condition</div>
  <div class="abs foot-link" style="left:585px;top:3584px">Privacy Policy</div>

  <div class="abs vline" style="left:758px;top:3442px;height:194px"></div>
  <div class="abs foot-title" style="left:822px;top:3441px">CONTACT INFO</div>
  <div class="abs contact-row" style="left:822px;top:3478px">
    <svg width="16" height="20" viewBox="0 0 24 30"><path fill="#0a6bbd" d="M12 0a10 10 0 0110 10c0 8-10 20-10 20S2 18 2 10A10 10 0 0112 0z"/><circle cx="12" cy="10" r="4" fill="#fff"/></svg>
    <span>212 Copperline Way<br>Sparks, NV 89437</span>
  </div>
  <div class="abs contact-row" style="left:822px;top:3544px">
    <svg width="20" height="14" viewBox="0 0 20 14" style="margin-top:5px"><rect width="20" height="14" fill="#0a6bbd"/><path d="M0 0l10 7 10-7" fill="none" stroke="#fff" stroke-width="1.6"/></svg>
    <span>admin@velotrinworks.com.au</span>
  </div>
  <div class="abs contact-row" style="left:822px;top:3587px">
    <svg width="18" height="18" viewBox="0 0 24 24" style="margin-top:3px"><path fill="#0a6bbd" d="M6.6 10.8a15 15 0 006.6 6.6l2.2-2.2c.3-.3.7-.4 1-.2 1.1.4 2.3.6 3.6.6.6 0 1 .4 1 1V20c0 .6-.4 1-1 1A17 17 0 013 4c0-.6.4-1 1-1h3.5c.6 0 1 .4 1 1 0 1.3.2 2.5.6 3.6.1.3 0 .7-.2 1z"/></svg>
    <span style="text-decoration:underline">(03) 9555 0127</span>
  </div>

  <div class="abs" style="left:107px;top:3642px;width:978px;height:1px;background:var(--line)"></div>
  <div class="abs foot-link" style="left:107px;top:3670px">© 2026 &nbsp;© 2026 Velotrin Works Construction, IncAll Rights Reserved.</div>
  <div class="abs foot-link" style="left:861px;top:3670px">Privacy &nbsp;&nbsp;|&nbsp;&nbsp; Terms &nbsp;&nbsp;|&nbsp;&nbsp; Disclaimer</div>
</footer>

</body>
</html>
```